WEBSITE DESIGN, VELTRA paint and panel

We are in need of a website for Veltra Paint & Panel based in Brisbane, Australia. We are a boutique Automotive Paint & Panel Company that provides services to all makes and models of vehicles. We have attached a logo that is still in draft stage but gives you an idea of the colour scheme and fonts and overall impact we are looking for. We are after a white background so this is clean and crisp whilst being sleek, modern and professional. The website must represent our slogan of Glowing finish on the Gleaming frame. The website must therefore be visually effective as our product is to get colour and placement on vehicle body's correct so the website must have this impact on our clients. We are after a widescreen webpage that is simple and logical to navigate. The final design should give clients the confidence that we can deliver on our promise.
Updates

Target Market(s)

Vehicle Owners who have a need for panel repairs and people who want to reinvigorate their car with a new coat of paint.

Industry/Entity Type

Car Repair

Coding

Coded - Design and coding required

Number of Pages Required

5+ page

Font styles to use
Sans Serif

Colors
ffffff
ffc214
000000

Requirements
Must have
• Page 1 - Home Page
• Page 2 - Our Process
• Page 3 - Private Customers
• Page 4 - Fleet & Corporate
• Page 5 - Insurance
• Page 6 - Get a Quote
• Page 7 - Connect (Contacts Page)
• Same font and colour scheme as the logo.
Should not have
• A typical mechanical/paint and panel layout which looks like a template website.

```html
<!DOCTYPE html>
<html lang="en">
<head>
<meta charset="utf-8">
<title>Veltra Paint &amp; Panel</title>
<link href="https://fonts.googleapis.com/css2?family=Roboto:wght@300;400;500;700&display=swap" rel="stylesheet">
<style>
:root{
  --accent:#c4b70c;
  --accent-dark:#a99d05;
  --ink:#222;
  --muted:#777;
  --line:#e3e3e3;
  --black:#0c0c0c;
  --footer:#f1f1f1;
  --white:#fff;
}
*{box-sizing:border-box;margin:0;padding:0}
html,body{width:1200px;height:2200px;overflow:hidden}
body{font-family:'Roboto',Arial,sans-serif;color:var(--ink);background:var(--white);font-size:13px;line-height:1.6}
.wrap{width:1000px;margin:0 auto;position:relative}

/* header */
.site-header{background:var(--black);height:92px}
.site-header .wrap{display:flex;align-items:center;justify-content:space-between;height:92px}
.brand{display:flex;align-items:center;gap:10px;color:var(--white);font-weight:500;letter-spacing:3px;font-size:15px;text-transform:uppercase}
.brand-dot{width:12px;height:12px;background:var(--accent)}
.brand small{display:block;font-size:9px;letter-spacing:2px;color:#bbb;font-weight:400}
.main-nav{display:flex;gap:30px}
.main-nav a{color:var(--white);text-decoration:none;font-size:11px}

/* hero */
.hero{height:548px;position:relative;background:linear-gradient(120deg,#dfe4ea 0%,#b9c3cf 35%,#4a5f8e 55%,#1d3aa8 70%,#2a3c78 100%)}
.hero-text{position:absolute;left:150px;top:330px;color:var(--white)}
.hero-text .lead{font-size:34px;font-weight:300;line-height:1.2}
.hero-text .strong{font-size:46px;font-weight:700;color:var(--accent);line-height:1.2}
.hero-arrow{position:absolute;top:355px;width:30px;height:30px;border-radius:50%;background:rgba(0,0,0,.55)}
.hero-arrow svg{display:block;margin:8px}
.hero-arrow.prev{left:40px}.hero-arrow.next{right:40px}
.hero-dots{position:absolute;bottom:18px;left:50%;transform:translateX(-50%);display:flex;gap:8px}
.hero-dots span{width:8px;height:8px;border-radius:50%;background:rgba(255,255,255,.6)}
.hero-dots span.on{background:var(--white)}

/* section heads */
.section-title{font-size:22px;font-weight:400;color:#333;display:flex;align-items:center;gap:16px}
.section-title::after{content:"";flex:1;height:1px;background:var(--line)}

/* process */
.process{padding-top:50px;height:360px}
.process .wrap{display:flex;gap:40px}
.process-intro{width:340px}
.process-intro .section-title::after{display:none}
.process-intro .kicker{margin-top:8px;color:#555;font-size:13px}
.process-intro p{margin-top:14px;color:var(--muted);font-size:11px}
.process-grid{flex:1;display:grid;grid-template-columns:1fr 1fr;gap:18px 20px;padding-top:34px}
.process-item{height:64px;border:1px solid var(--line);display:flex;align-items:center;padding-left:18px;gap:16px;position:relative}
.process-item span{color:var(--accent);font-size:12px}
.process-item .tab{position:absolute;right:0;top:0;bottom:0;width:34px;background:var(--accent);display:flex;align-items:center;justify-content:center}

/* services */
.services{height:440px}
.service-cards{display:flex;gap:35px;margin-top:30px}
.service-card{width:310px;border:1px solid var(--line);text-align:center;padding-bottom:20px}
.service-card .photo{height:172px}
.service-card h3{font-size:14px;font-weight:500;margin-top:18px}
.service-card p{font-size:10px;color:var(--muted);padding:8px 24px 0}
.card-actions{display:flex;justify-content:center;gap:12px;margin-top:16px}
.btn{font-size:10px;padding:6px 14px;min-width:86px;text-align:center}
.btn-outline{border:1px solid var(--accent);color:var(--accent)}
.btn-solid{background:var(--accent);color:var(--white)}

/* testimonials */
.testimonials{height:250px;padding-top:30px}
.testimonial-row{display:flex;gap:60px;margin-top:30px}
.testimonial{display:flex;gap:24px;width:470px}
.avatar{width:88px;height:88px;border-radius:50%;flex:none;background:linear-gradient(160deg,#d9c7b4,#8a7664)}
.testimonial p{font-size:10px;color:#999}
.testimonial .who{margin-top:8px;font-size:10px;color:var(--accent)}
.testimonial .role{font-size:9px;color:#aaa}
.slider-dots{position:absolute;right:0;top:3px;display:flex;gap:5px}
.slider-dots span{width:6px;height:6px;border-radius:50%;background:#ccc}

/* footer */
.site-footer{background:var(--footer);height:310px;padding-top:34px}
.site-footer .wrap{display:flex;gap:40px}
.footer-col h4{font-size:11px;font-weight:500;text-transform:uppercase;color:#444;margin-bottom:14px}
.footer-col p,.footer-col li{font-size:10px;color:#777}
.footer-col ul{list-style:none}
.footer-col li{display:flex;align-items:center;gap:8px;margin-bottom:7px}
.contact{width:260px}
.contact li svg{flex:none}
.links{width:230px}
.bullet{width:8px;height:8px;background:var(--accent)}
.social{width:150px}
.social .ico{width:16px;height:16px;border-radius:50%;background:#3f3f3f}
.quick{flex:1}
.field{height:26px;background:var(--white);border:1px solid #ddd;font-size:9px;color:#aaa;padding:5px 8px;margin-bottom:8px}
.field.area{height:62px}
.quick .btn-solid{width:100%;font-size:10px;padding:7px}

/* bottom */
.bottom-bar{background:var(--black);height:218px;text-align:center;padding-top:44px;color:#888}
.bottom-bar .brand{justify-content:center}
.bottom-nav{display:flex;justify-content:center;gap:22px;margin-top:18px}
.bottom-nav a{color:#aaa;font-size:9px;text-decoration:none}
.copyright{font-size:9px;margin-top:8px;color:#666}
</style>
</head>
<body>

<header class="site-header">
  <div class="wrap">
    <div class="brand"><span class="brand-dot"></span><div>VELTRA<small>paint and panel</small></div></div>
    <nav class="main-nav">
      <a href="#">Home</a><a href="#">Our Process</a><a href="#">Private Customers</a><a href="#">Fleet &amp; Corporate Insurance</a><a href="#">Get a Quote</a><a href="#">Contact</a>
    </nav>
  </div>
</header>

<section class="hero" role="img" aria-label="Painter in protective suit spraying a blue car body in a paint booth">
  <div class="hero-text">
    <div class="lead">Glowing finish on the</div>
    <div class="strong">Gleaming frame</div>
  </div>
  <div class="hero-arrow prev"><svg width="14" height="14" viewBox="0 0 14 14"><path d="M9 2 4 7l5 5" fill="none" stroke="#fff" stroke-width="2"/></svg></div>
  <div class="hero-arrow next"><svg width="14" height="14" viewBox="0 0 14 14"><path d="M5 2l5 5-5 5" fill="none" stroke="#fff" stroke-width="2"/></svg></div>
  <div class="hero-dots"><span class="on"></span><span></span><span></span></div>
</section>

<section class="process">
  <div class="wrap">
    <div class="process-intro">
      <h2 class="section-title">Our Process</h2>
      <p class="kicker">Every vehicle moves through a careful, tested path from first look to final polish.</p>
      <p>We inspect each panel, match the factory colour, prepare the surface and spray in a clean booth. Every finish is checked under bright light before handover, so your car leaves looking as good as the day it was built.</p>
    </div>
    <div class="process-grid">
      <div class="process-item">
        <svg width="34" height="22" viewBox="0 0 34 22"><path d="M3 14l3-8h22l3 8v5H3z" fill="#333"/><circle cx="9" cy="19" r="3" fill="#333"/><circle cx="25" cy="19" r="3" fill="#333"/></svg>
        <span>Get a free damage review</span>
        <div class="tab"><svg width="10" height="12" viewBox="0 0 10 12"><path d="M2 1l5 5-5 5" fill="none" stroke="#fff" stroke-width="2"/></svg></div>
      </div>
      <div class="process-item">
        <svg width="30" height="26" viewBox="0 0 30 26"><path d="M1 2h5l4 14h15l3-10H8" fill="none" stroke="#333" stroke-width="2.5"/><circle cx="12" cy="22" r="2.5" fill="#333"/><circle cx="23" cy="22" r="2.5" fill="#333"/></svg>
        <span>Get a clear fixed quote</span>
        <div class="tab"><svg width="10" height="12" viewBox="0 0 10 12"><path d="M2 1l5 5-5 5" fill="none" stroke="#fff" stroke-width="2"/></svg></div>
      </div>
      <div class="process-item">
        <svg width="28" height="28" viewBox="0 0 28 28"><circle cx="14" cy="14" r="11" fill="none" stroke="#333" stroke-width="3"/><circle cx="14" cy="14" r="3" fill="#333"/><path d="M3 14h8M17 14h8M14 17v8" stroke="#333" stroke-width="3"/></svg>
        <span>Get an exact colour match</span>
        <div class="tab"><svg width="10" height="12" viewBox="0 0 10 12"><path d="M2 1l5 5-5 5" fill="none" stroke="#fff" stroke-width="2"/></svg></div>
      </div>
      <div class="process-item">
        <svg width="32" height="24" viewBox="0 0 32 24"><circle cx="10" cy="7" r="5" fill="#333"/><circle cx="22" cy="7" r="5" fill="#333"/><path d="M1 23c0-7 4-10 9-10s9 3 9 10zM13 23c0-7 4-10 9-10s9 3 9 10z" fill="#333"/></svg>
        <span>Get a friendly handover</span>
        <div class="tab"><svg width="10" height="12" viewBox="0 0 10 12"><path d="M2 1l5 5-5 5" fill="none" stroke="#fff" stroke-width="2"/></svg></div>
      </div>
    </div>
  </div>
</section>

<section class="services">
  <div class="wrap">
    <h2 class="section-title">Our Services</h2>
    <div class="service-cards">
      <article class="service-card">
        <div class="photo" role="img" aria-label="Freshly sprayed red car panel" style="background:linear-gradient(135deg,#f4e9e9,#c92a2a 60%,#7c1010)"></div>
        <h3>Full Colour Respray</h3>
        <p>Complete colour changes and fresh coats with a deep, even gloss that lasts for years on the road.</p>
        <div class="card-actions"><span class="btn btn-outline">GET A QUOTE</span><span class="btn btn-solid">READ MORE</span></div>
      </article>
      <article class="service-card">
        <div class="photo" role="img" aria-label="Technician working on an engine bay" style="background:linear-gradient(135deg,#8e9aa6,#3e4854 60%,#1d232a)"></div>
        <h3>Panel Beating Repairs</h3>
        <p>Dents, creases and crash damage reshaped by hand so every line of the body sits true again.</p>
        <div class="card-actions"><span class="btn btn-outline">GET A QUOTE</span><span class="btn btn-solid">READ MORE</span></div>
      </article>
      <article class="service-card">
        <div class="photo" role="img" aria-label="Mechanic fitting parts under a red vehicle" style="background:linear-gradient(135deg,#b8322c,#5a1a16 55%,#2b2b2b)"></div>
        <h3>Fleet &amp; Insurance Work</h3>
        <p>Fast turnaround for business fleets and insurance claims, with updates at every stage of repair.</p>
        <div class="card-actions"><span class="btn btn-outline">GET A QUOTE</span><span class="btn btn-solid">READ MORE</span></div>
      </article>
    </div>
  </div>
</section>

<section class="testimonials">
  <div class="wrap">
    <h2 class="section-title">Private Customers</h2>
    <div class="slider-dots" style="top:12px"><span></span><span></span></div>
    <div class="testimonial-row">
      <div class="testimonial">
        <div class="avatar" role="img" aria-label="Customer portrait"></div>
        <div>
          <p>The team brought my old sedan back to life. The new paint is flawless and the colour matches perfectly on every panel. Friendly staff and the job was done right on time.</p>
          <div class="who">Daniel Harwood</div>
          <div class="role">Private Customer</div>
        </div>
      </div>
      <div class="testimonial">
        <div class="avatar" role="img" aria-label="Customer portrait" style="background:linear-gradient(160deg,#e2cbb4,#6b4a36)"></div>
        <div>
          <p>After a minor accident I was worried about the finish, but you cannot tell anything happened. Clear quote, honest advice and a shine that turns heads wherever I park.</p>
          <div class="who">Megan Loxley</div>
          <div class="role">Private Customer</div>
        </div>
      </div>
    </div>
  </div>
</section>

<footer class="site-footer">
  <div class="wrap">
    <div class="footer-col contact">
      <h4>Contact Us</h4>
      <p style="margin-bottom:12px">Drop by our workshop or give us a call. We are open six days a week for quotes and repairs.</p>
      <ul>
        <li><svg width="10" height="12" viewBox="0 0 10 12"><path d="M5 11S1 7 1 4.5a4 4 0 0 1 8 0C9 7 5 11 5 11z" fill="#c4b70c"/></svg>14 Harlow Street, Eastbrook QLD 4102</li>
        <li><svg width="10" height="10" viewBox="0 0 10 10"><path d="M2 1l2 2-1 1.5c.8 1.3 1.7 2.2 3 3L7.5 6l2 2-1.5 1.5C4.5 9 1 5.5.5 2.5z" fill="#c4b70c"/></svg>(07) 3555 0192</li>
        <li><svg width="10" height="8" viewBox="0 0 10 8"><rect x=".5" y=".5" width="9" height="7" fill="none" stroke="#c4b70c"/><path d="M.5.5 5 4 9.5.5" fill="none" stroke="#c4b70c"/></svg>hello@veltrapaint.example</li>
      </ul>
    </div>
    <div class="footer-col links">
      <h4>Our Services</h4>
      <ul>
        <li><span class="bullet"></span>Fleet &amp; Panel Repairs</li>
        <li><span class="bullet"></span>Scratch and chip touch ups</li>
        <li><span class="bullet"></span>Full colour resprays</li>
        <li><span class="bullet"></span>Insurance claim repairs</li>
        <li><span class="bullet"></span>Fleet &amp; Corporate Work</li>
      </ul>
    </div>
    <div class="footer-col social">
      <h4>Follow Us</h4>
      <ul>
        <li><span class="ico"></span>Friendwall</li>
        <li><span class="ico"></span>Chirper</li>
        <li><span class="ico"></span>Circlenet</li>
        <li><span class="ico"></span>Worklink</li>
      </ul>
    </div>
    <div class="footer-col quick">
      <h4>Quick Contact</h4>
      <div class="field">Your name</div>
      <div class="field">Your e-mail</div>
      <div class="field area">Your Message</div>
      <div class="btn btn-solid">SEND MESSAGE</div>
    </div>
  </div>
</footer>

<section class="bottom-bar">
  <div class="brand"><span class="brand-dot"></span><div>VELTRA<small>paint and panel</small></div></div>
  <nav class="bottom-nav">
    <a href="#">Home</a><a href="#">Our Process</a><a href="#">Private Customers</a><a href="#">Fleet &amp; Corporate Insurance</a><a href="#">Get a Quote</a><a href="#">Contact</a>
  </nav>
  <div class="copyright">Copyright &copy; Veltra Paint &amp; Panel. All rights reserved.</div>
</section>

</body>
</html>
```